BrivoTerna. Lantern of the Steady Harvest. Business card

Professional business card for BrivoTerna (Lantern of the Steady Harvest)
My rationale: Strategy-> Execution-> Results-> Value that lead to the BrivoTerna name: We put the Lantern of the Steady Harvest.
We deliver value to our customers helping them at defining a good strategy (cyan arrow). 90% of well formulated strategies fail due to poor execution so we also consider strategical execution very important (green arrow). Due to the execution we obtain the results (blue arrow). Finally, the results provide feedback to redefine strategy, and the new strategy has to be executed and new results obtained providing new feedback and on and on. It's like a wheel that finally, must create corporate value: value for shareholders, staholders, employees, providers...-

Target Market(s)

CEOs and steering comitees , invewrnent funds

Industry/Entity Type

Business Consultant

Contact Information for Business Card

Teodoro Vinsquel
CEO & Founder
teodoro.vinsquel@brivoterna-example.com
Mobile: +34 655.803.912
www.brivoterna-example.com

Colors

Designer to choose colors to be used in the design.

Requirements
Nice to have
• Nice to hace the words: Strategy, execution, results
• Nice to vave the claim: Lantern of the Steady Harvest
• The three colors should be shown:
• cyan for STRATEGY
• green for EXECUTION
• blue for RESULTS
Should not have
• Complete black background

```html
<!DOCTYPE html>
<html lang="en">
<head>
<meta charset="utf-8">
<title>BrivoTerna — Business Card</title>
<link rel="stylesheet" href="https://fonts.googleapis.com/css2?family=Open+Sans:ital,wght@0,400;0,700;0,800;1,800&display=swap">
<style>
  :root {
    --stage: #2e2f33;
    --brand-blue: #0a3597;
    --deep-blue: #062a7e;
    --growth-green: #8cc63f;
    --strategy-cyan: #2fa8e6;
    --paper: #ffffff;
    --ink-dark: #222222;
  }
  * { margin: 0; padding: 0; box-sizing: border-box; }
  html, body {
    width: 1200px; height: 960px; overflow: hidden;
    background: var(--stage);
    font-family: "Open Sans", Arial, sans-serif;
  }
  .card {
    position: absolute;
    left: 310px;
    width: 580px; height: 375px;
    border-radius: 4px;
    overflow: hidden;
    box-shadow: 0 10px 30px rgba(0,0,0,.35);
  }
  /* Back side */
  .card--back { top: 80px; background: var(--brand-blue); }
  .card--back .brand-name {
    position: absolute; left: 0; right: 0; top: 140px;
    text-align: center;
    font-weight: 800; font-size: 64px; letter-spacing: -1px;
    color: var(--paper);
  }
  .card--back .web {
    position: absolute; left: 0; right: 0; top: 240px;
    text-align: center;
    font-size: 15px; letter-spacing: 3px;
    color: var(--paper);
  }
  /* Front side */
  .card--front { top: 505px; background: var(--paper); }
  .card--front .wave-band { position: absolute; inset: 0; }
  .card--front .brand-name {
    position: absolute; left: 36px; top: 62px;
    font-weight: 800; font-size: 50px; letter-spacing: -1px;
    color: var(--brand-blue);
  }
  .person {
    position: absolute; right: 34px; top: 118px; text-align: right;
  }
  .person__name {
    font-weight: 800; font-style: italic; font-size: 21px;
    color: var(--brand-blue);
  }
  .person__role { font-size: 12px; color: var(--ink-dark); margin-top: 2px; }
  .contacts {
    position: absolute; right: 28px; top: 264px;
    list-style: none; text-align: right;
    color: var(--paper); font-size: 13px; line-height: 21px;
  }
  .contacts li { display: flex; justify-content: flex-end; align-items: center; gap: 8px; }
  .contacts svg { width: 13px; height: 13px; flex: none; }
  .contacts .address { padding-right: 21px; }
</style>
</head>
<body>

<section class="card card--back" aria-label="Business card, back">
  <div class="brand-name">BrivoTerna</div>
  <div class="web">www.brivoterna-example.com</div>
</section>

<section class="card card--front" aria-label="Business card, front">
  <svg class="wave-band" viewBox="0 0 580 375" role="img" aria-label="Curved wave ribbon in green, white and cyan over the blue lower band">
    <defs>
      <linearGradient id="bandTone" x1="0" y1="0" x2="1" y2="0">
        <stop offset="0" stop-color="var(--deep-blue)"/>
        <stop offset="1" stop-color="var(--brand-blue)"/>
      </linearGradient>
    </defs>
    <path d="M0 165 C 150 225 320 255 580 215 L580 375 L0 375 Z" fill="url(#bandTone)"/>
  </svg>

  <div class="brand-name">BrivoTerna</div>

  <div class="person">
    <div class="person__name">Teodoro Vinsquel</div>
    <div class="person__role">CEO &amp; Founder</div>
  </div>

  <ul class="contacts">
    <li>+34 655.803.912
      <svg viewBox="0 0 13 13" aria-hidden="true"><rect x="3" y="0.8" width="7" height="11.4" rx="1.2" fill="none" stroke="var(--growth-green)" stroke-width="1.3"/><circle cx="6.5" cy="10" r="0.8" fill="var(--growth-green)"/></svg>
    </li>
    <li>www.brivoterna-example.com
      <svg viewBox="0 0 13 13" aria-hidden="true"><g fill="none" stroke="var(--growth-green)" stroke-width="1.1"><circle cx="6.5" cy="6.5" r="5.6"/><ellipse cx="6.5" cy="6.5" rx="2.4" ry="5.6"/><path d="M1 6.5h11M2 3.6h9M2 9.4h9"/></g></svg>
    </li>
    <li>teodoro.vinsquel@brivoterna-example.com
      <svg viewBox="0 0 13 13" aria-hidden="true"><rect x="0.5" y="2.5" width="12" height="8" fill="var(--growth-green)"/><path d="M0.8 2.8 6.5 7.3 12.2 2.8" fill="none" stroke="var(--brand-blue)" stroke-width="1"/></svg>
    </li>
    <li class="address">Carrer Olvenda 47, Valdoria, 08214, Spain</li>
  </ul>
</section>

</body>
</html>
```